Local business providing residential house cleaning services

We need a business card design that is "cute" or "cartoonish" while still maintaining a professional appeal. Tidal Sweepers is the name. We would like to use a "pin up girl" or maid next to the name with a broom or vacuum cleaner. We want the look to have a 50's American look to it. We are not sure if we want the pin up girl in a maid outfit or with a broom or vacuum cleaner but we hope some of you will be able to take these ideas and be creative. If you have any questions at all please don't hesitate to message me so that we can get the best design possible. Thank you very much and I look forward to seeing some designs! Mira Hollister

Target Market(s)

Upper class Americans that are busy and have money and want to come home to a clean house.

Industry/Entity Type

Cleaning Service

Contact Information for Business Card

Pin up girl incorporated into the card is a must.

Font styles to use
Decorative
Script

Requirements
Must have
• Pin up girl
Nice to have
• A crown used on the Q possibly.

```html
<!DOCTYPE html>
<html lang="en">
<head>
<meta charset="utf-8">
<title>Tidal Sweepers – Business Card</title>
<link href="https://fonts.googleapis.com/css2?family=Lora:ital,wght@0,700;1,400&display=swap" rel="stylesheet">
<style>
  :root {
    --page-bg: #eeeff0;
    --brand-orange: #f39a1b;
    --dot-tint: #f7b455;
    --ink: #2b2626;
    --paper: #ffffff;
  }
  html, body {
    margin: 0;
    padding: 0;
    width: 928px;
    height: 1200px;
    overflow: hidden;
    background: var(--page-bg);
  }
  .canvas {
    position: relative;
    width: 928px;
    height: 1200px;
  }
  .business-card {
    position: absolute;
    left: 170px;
    top: 145px;
    width: 508px;
    height: 880px;
    border-radius: 41px;
    overflow: hidden;
    background: var(--brand-orange);
  }
  .business-card svg { display: block; }
  .pattern-field { fill: url(#pattern-tone); }
  .frame-band { fill: var(--brand-orange); stroke: var(--ink); stroke-width: 2.5; }
  .frame-rule { fill: none; stroke: var(--paper); stroke-width: 2; }
  .frame-panel { fill: var(--paper); stroke: var(--ink); stroke-width: 2; }
  .brand-name {
    font-family: "Lora", Georgia, serif;
    font-weight: 700;
    font-size: 66px;
    fill: var(--ink);
  }
  .holder-name, .contact-line {
    font-family: "Lora", Georgia, serif;
    font-style: italic;
    font-weight: 400;
    fill: var(--ink);
    text-anchor: middle;
  }
  .holder-name { font-size: 35px; }
  .contact-line { font-size: 32px; }
  .contact-line.email { font-size: 29px; }
  .contact-icon { fill: none; stroke: var(--brand-orange); stroke-width: 2.5; stroke-linejoin: round; }
</style>
</head>
<body>
<div class="canvas">
  <div class="business-card">
    <svg viewBox="0 0 615 1065" width="508" height="880" xmlns="http://www.w3.org/2000/svg">
      <defs>
        <path id="bracket-frame" d="M308,60 C325,78 350,88 380,88 L490,88 Q500,88 500,100 C500,120 515,130 535,130 Q548,130 548,142 L548,470 C548,500 560,515 585,525 C560,535 548,550 548,580 L548,905 Q548,918 535,918 C515,918 500,928 500,948 Q500,960 490,960 L380,960 C350,960 325,970 308,992 C291,970 266,960 236,960 L126,960 Q116,960 116,948 C116,928 101,918 81,918 Q68,918 68,905 L68,580 C68,550 56,535 31,525 C56,515 68,500 68,470 L68,142 Q68,130 81,130 C101,130 116,120 116,100 Q116,88 126,88 L236,88 C266,88 291,78 308,60 Z"/>
        <radialGradient id="pattern-tone" cx="0.5" cy="0.5" r="0.75">
          <stop offset="0" stop-color="#f39a1b"/>
          <stop offset="1" stop-color="#f7b455"/>
        </radialGradient>
        <linearGradient id="figure-tone" x1="0" y1="0" x2="0" y2="1">
          <stop offset="0" stop-color="#2b2626"/>
          <stop offset="0.5" stop-color="#5a3f22"/>
          <stop offset="1" stop-color="#f39a1b"/>
        </linearGradient>
      </defs>

      <!-- background pattern area -->
      <rect class="pattern-field" x="0" y="0" width="615" height="1065" role="img" aria-label="Light orange polka-dot pattern on orange"/>

      <!-- bracket frame -->
      <use href="#bracket-frame" class="frame-band"/>
      <use href="#bracket-frame" class="frame-rule" transform="translate(308 525) scale(.955 .975) translate(-308 -525)"/>
      <use href="#bracket-frame" class="frame-panel" transform="translate(308 525) scale(.92 .955) translate(-308 -525)"/>

      <!-- brand -->
      <g role="img" aria-label="Illustration of a 1950s pin-up maid in a polka-dot apron holding a feather duster">
        <rect x="395" y="172" width="100" height="215" rx="28" fill="url(#figure-tone)"/>
      </g>
      <text class="brand-name" x="120" y="405">Tidal</text>
      <text class="brand-name" x="120" y="485">Sweepers</text>

      <!-- card holder -->
      <text class="holder-name" x="308" y="620">Mira Hollister</text>

      <!-- phone -->
      <g class="contact-icon">
        <rect x="298" y="655" width="20" height="32" rx="3"/>
        <line x1="298" y1="680" x2="318" y2="680"/>
      </g>
      <text class="contact-line" x="308" y="735">501-555-0147</text>

      <!-- email -->
      <g class="contact-icon">
        <rect x="292" y="772" width="32" height="22" rx="2"/>
        <path d="M292,773 L308,786 L324,773"/>
      </g>
      <text class="contact-line email" x="308" y="842">mira.hollister25@mailbox.com</text>
    </svg>
  </div>
</div>
</body>
</html>
```